Business card design needed with logo

My business is called PLQ Works & it is targeted towards mobile equipment maintenance in the Mining and civil industry. My work involves maintenance planning and maintenance management plus also supply tradespeople on a labour hire basis. We can provide from basic shut-down machine rebuild plans to complete rebuild services supply plans and labour to anywhere in Australia. I would like to use the colours Black, Red and Grey, I had done a desgin as attached but doesn't really explain what we do and gears don't embroider well onto shirts.
Updates

I also wanted to see the something replace the gears maybe just making the PLQ lettering look a bit different or put together differently 

Hello I have extended the deadline by a few extra days as I would like to update details on the front of card, details below & can be put which ever way looks good;

Mark Tilley
Director
0417295361
PLQ@mailbay.com.au
www.plqworks-example.com.au

On the back of the card I would like to have the below printed;

Capable of providing, but not limited to, across Australia:
- Contract Maintenance Planning.
- Skilled Mobile Maintenance labour hire.
- New machine build specifications. 
- Plant risk assessments and inspections.
- Shut down and rebuild program planning.
- Preventative maintenance tasks, including build of materials lists, creation and review.

Target Market(s)

Contractors and companies that use small and large earthmoving and mining machines

Industry/Entity Type

Business

Contact Information for Business Card

Trading name is PLQ Works
My name and title is
Mark Tilley Director
0417 295 361
PLQ@mailbay.com.au

Logo Text

PLQ

```html
<!DOCTYPE html>
<html lang="en">
<head>
<meta charset="utf-8">
<title>PLQ Works – Business Card</title>
<link rel="stylesheet" href="https://fonts.googleapis.com/css2?family=Oswald:wght@500;600&family=Open+Sans:wght@400;600&display=swap">
<style>
  :root {
    --backdrop: #3b4856;
    --card-white: #f1f1f1;
    --band-grey: #8a8a8a;
    --accent-red: #d9352a;
    --icon-orange: #e0613a;
    --text-dark: #3a3a3a;
    --text-mid: #555555;
    --back-dark: #2a2f37;
    --back-sheen: #3a414c;
    --back-text: #d6d9dd;
    --metal-light: #e4e6e8;
    --metal-mid: #c3c6ca;
  }
  * { box-sizing: border-box; margin: 0; padding: 0; }
  html, body { width: 1200px; height: 1000px; overflow: hidden; }
  body {
    background: var(--backdrop);
    position: relative;
    font-family: "Open Sans", Arial, sans-serif;
  }
  .card {
    position: absolute;
    left: 250px;
    width: 700px;
    height: 400px;
    overflow: hidden;
    box-shadow: 0 8px 22px rgba(0,0,0,0.35);
  }

  /* Front */
  .card-front { top: 60px; background: var(--card-white); }
  .front-side-band {
    position: absolute; left: 0; top: 0; width: 48px; height: 100%;
    background: var(--band-grey);
  }
  .front-side-accent {
    position: absolute; left: 0; top: 262px; width: 150px; height: 26px;
    background: var(--accent-red);
  }
  .front-corner-block {
    position: absolute; right: 0; top: 30px; width: 48px; height: 52px;
    background: var(--band-grey);
  }
  .front-red-band {
    position: absolute; right: 0; top: 160px; width: 370px; height: 36px;
    background: var(--accent-red);
  }
  .holder {
    position: absolute; right: 62px; top: 30px; text-align: right;
  }
  .holder-name {
    font-family: "Oswald", "Arial Narrow", sans-serif;
    font-weight: 600; font-size: 34px; line-height: 1;
    color: var(--accent-red); text-transform: uppercase; letter-spacing: 0.5px;
  }
  .holder-title {
    font-size: 13px; color: var(--text-mid); margin-top: 2px;
  }
  .trading-name {
    position: absolute; left: 168px; top: 222px;
    font-family: "Oswald", "Arial Narrow", sans-serif;
    font-weight: 600; font-size: 46px; line-height: 1;
    color: var(--text-dark); text-transform: uppercase;
  }
  .contact-list {
    position: absolute; left: 204px; top: 294px; list-style: none;
  }
  .contact-item {
    display: flex; align-items: center; gap: 10px;
    font-size: 15px; line-height: 20px; color: var(--text-mid); margin-bottom: 7px;
  }
  .contact-icon { width: 16px; height: 16px; flex: none; }

  /* Back */
  .card-back {
    top: 540px;
    background: linear-gradient(90deg, var(--back-dark) 0%, var(--back-dark) 35%, var(--back-sheen) 45%, var(--back-dark) 55%, var(--back-dark) 100%);
  }
  .services-heading {
    position: absolute; left: 40px; right: 40px; top: 34px;
    text-align: center;
    font-size: 14px; font-weight: 600; line-height: 20px;
    color: var(--back-text);
  }
  .back-metal-band {
    position: absolute; left: 0; top: 88px; width: 100%; height: 120px;
    background: linear-gradient(90deg, var(--metal-mid) 0%, var(--metal-light) 35%, #f4f5f6 55%, var(--metal-mid) 100%);
    display: flex; align-items: center; justify-content: center; gap: 18px;
  }
  .brand-name {
    font-family: "Oswald", "Arial Narrow", sans-serif;
    font-weight: 600; font-size: 76px; line-height: 1;
    color: var(--text-dark); letter-spacing: 2px;
  }
  .brand-dot {
    width: 42px; height: 42px; border-radius: 50%;
    background: var(--band-grey);
  }
  .services-list {
    position: absolute; left: 48px; right: 40px; top: 230px;
    list-style: none;
  }
  .service-item {
    position: relative; padding-left: 16px;
    font-size: 13px; line-height: 24px; color: var(--back-text);
  }
  .service-item::before {
    content: ""; position: absolute; left: 0; top: 9px;
    width: 6px; height: 6px; background: var(--accent-red);
  }
</style>
</head>
<body>
  <section class="card card-front" aria-label="Business card front">
    <div class="front-side-band"></div>
    <div class="front-side-accent"></div>
    <div class="front-corner-block"></div>
    <div class="front-red-band"></div>

    <div class="holder">
      <p class="holder-name">Mark Tilley</p>
      <p class="holder-title">Director</p>
    </div>

    <h1 class="trading-name">PLQ Works</h1>

    <ul class="contact-list">
      <li class="contact-item">
        <svg class="contact-icon" viewBox="0 0 16 16" aria-hidden="true">
          <circle cx="8" cy="8" r="7.2" fill="none" stroke="#e0613a" stroke-width="1.4"/>
          <path d="M5.4 4.5l1.3 1.6-.7 1c.5 1 1.3 1.8 2.3 2.3l1-.7 1.6 1.3-.7 1.2c-2.6-.3-5.1-2.8-5.4-5.4z" fill="#e0613a"/>
        </svg>
        <span>0417 295 361</span>
      </li>
      <li class="contact-item">
        <svg class="contact-icon" viewBox="0 0 16 16" aria-hidden="true">
          <rect x="1.5" y="3.5" width="13" height="9" rx="1" fill="none" stroke="#e0613a" stroke-width="1.4"/>
          <path d="M2 4.2l6 4.5 6-4.5" fill="none" stroke="#e0613a" stroke-width="1.4"/>
        </svg>
        <span>PLQ@mailbay.com.au</span>
      </li>
      <li class="contact-item">
        <svg class="contact-icon" viewBox="0 0 16 16" aria-hidden="true">
          <circle cx="8" cy="8" r="7" fill="none" stroke="#e0613a" stroke-width="1.3"/>
          <ellipse cx="8" cy="8" rx="3" ry="7" fill="none" stroke="#e0613a" stroke-width="1.1"/>
          <path d="M1 8h14" stroke="#e0613a" stroke-width="1.1"/>
        </svg>
        <span>www.plqworks-example.com.au</span>
      </li>
    </ul>
  </section>

  <section class="card card-back" aria-label="Business card back">
    <p class="services-heading">Capable of providing, but not limited to, across Australia:</p>
    <div class="back-metal-band">
      <span class="brand-name">PLQ</span>
      <span class="brand-dot" aria-hidden="true"></span>
    </div>
    <ul class="services-list">
      <li class="service-item">Contract Maintenance Planning.</li>
      <li class="service-item">Skilled Mobile Maintenance labour hire.</li>
      <li class="service-item">New machine build specifications.</li>
      <li class="service-item">Plant risk assessments and inspections.</li>
      <li class="service-item">Shut down and rebuild program planning.</li>
      <li class="service-item">Preventative maintenance tasks, including build of materials lists, creation and review.</li>
    </ul>
  </section>
</body>
</html>
```